Veldmark Supplies Business Card

Professional business card that stand out to our potential customers. Front and back with clean modern design

Industry/Entity Type

Oil and gas

Contact Information for Business Card

Name, address, website , office phone and cell number

Requirements
Must have
• Editable files for each employee

```html
<!DOCTYPE html>
<html lang="en">
<head>
<meta charset="utf-8">
<title>Veldmark Supplies Business Card</title>
<link href="https://fonts.googleapis.com/css2?family=Lato:wght@400;700;900&display=swap" rel="stylesheet">
<style>
  :root {
    --stage: #3a3a3a;
    --card: #161616;
    --red: #ff0000;
    --cyan: #00b4d8;
    --ink: #ffffff;
    --rule: #d8d8d8;
  }
  * { box-sizing: border-box; margin: 0; padding: 0; }
  html, body { width: 1200px; height: 694px; overflow: hidden; }
  body {
    background: var(--stage);
    font-family: "Lato", Arial, sans-serif;
    color: var(--ink);
    position: relative;
  }
  .card {
    position: absolute;
    top: 192px;
    width: 540px;
    height: 310px;
    background: var(--card);
    border-radius: 20px;
    overflow: hidden;
  }
  .card--front { left: 40px; }
  .card--back { left: 620px; }

  /* Front */
  .brand {
    display: flex;
    align-items: center;
    gap: 14px;
  }
  .brand__square {
    width: 34px;
    height: 34px;
    background: var(--red);
  }
  .brand__name {
    font-weight: 900;
    color: var(--red);
    text-transform: uppercase;
    letter-spacing: 2px;
  }
  .card--front .brand {
    position: absolute;
    left: 0; right: 0; top: 0; bottom: 0;
    justify-content: center;
  }
  .card--front .brand__name { font-size: 34px; }
  .card--front .brand__square { width: 44px; height: 44px; }

  /* Back */
  .card--back .brand {
    position: absolute;
    right: 36px;
    top: 52px;
  }
  .card--back .brand__name { font-size: 20px; letter-spacing: 1.5px; }
  .card--back .brand__square { width: 26px; height: 26px; }

  .person {
    position: absolute;
    left: 36px;
    top: 118px;
  }
  .person__name {
    font-size: 26px;
    font-weight: 700;
    color: var(--red);
    line-height: 1.1;
  }
  .person__role {
    font-size: 15px;
    margin-top: 4px;
  }
  .divider {
    position: absolute;
    left: 36px;
    right: 36px;
    top: 178px;
    height: 1px;
    background: var(--rule);
  }
  .contact-list {
    position: absolute;
    list-style: none;
    font-size: 14px;
    line-height: 1;
  }
  .contact-list li {
    display: flex;
    align-items: center;
    gap: 10px;
    height: 24px;
  }
  .contact-list svg { width: 16px; height: 16px; flex: none; fill: var(--cyan); }
  .contact-list--personal { left: 36px; top: 190px; }
  .contact-list--company { right: 36px; top: 190px; text-align: right; }
  .contact-list--company li { justify-content: flex-end; align-items: flex-start; }
  .contact-list--company .address { line-height: 20px; height: auto; }
  .contact-list--company .address svg { margin-top: 2px; }

  .edge-band {
    position: absolute;
    left: 0; right: 0; bottom: 0;
    height: 8px;
    display: flex;
  }
  .edge-band__red { flex: 3; background: var(--red); }
  .edge-band__cyan { flex: 1; background: var(--cyan); }
</style>
</head>
<body>

  <section class="card card--front" aria-label="Card front">
    <div class="brand">
      <span class="brand__square"></span>
      <span class="brand__name">Veldmark Supplies</span>
    </div>
  </section>

  <section class="card card--back" aria-label="Card back">
    <div class="brand">
      <span class="brand__square"></span>
      <span class="brand__name">Veldmark Supplies</span>
    </div>

    <div class="person">
      <p class="person__name">Martin Hale</p>
      <p class="person__role">Owner</p>
    </div>

    <div class="divider"></div>

    <ul class="contact-list contact-list--personal">
      <li>
        <svg viewBox="0 0 24 24" aria-hidden="true"><path d="M6.6 10.8a15.1 15.1 0 0 0 6.6 6.6l2.2-2.2a1 1 0 0 1 1-.25 11.4 11.4 0 0 0 3.6.57 1 1 0 0 1 1 1V20a1 1 0 0 1-1 1A17 17 0 0 1 3 4a1 1 0 0 1 1-1h3.5a1 1 0 0 1 1 1c0 1.25.2 2.45.57 3.57a1 1 0 0 1-.25 1z"/></svg>
        <span>044-123 456 789</span>
      </li>
      <li>
        <svg viewBox="0 0 24 24" aria-hidden="true"><path d="M7 1h10a2 2 0 0 1 2 2v18a2 2 0 0 1-2 2H7a2 2 0 0 1-2-2V3a2 2 0 0 1 2-2zm0 3v14h10V4zm5 15.5a1 1 0 1 0 0 2 1 1 0 0 0 0-2z"/></svg>
        <span>044-123 456 789</span>
      </li>
      <li>
        <svg viewBox="0 0 24 24" aria-hidden="true"><path d="M2 5h20v14H2zm2 2v.5l8 5 8-5V7z"/></svg>
        <span>info@veldmarksupplies.com</span>
      </li>
    </ul>

    <ul class="contact-list contact-list--company">
      <li>
        <span>www.veldmarksupplies.com</span>
        <svg viewBox="0 0 24 24" aria-hidden="true"><path d="M12 2a10 10 0 1 0 0 20 10 10 0 0 0 0-20zm0 2c1 0 2.3 2 2.8 5H9.2C9.7 6 11 4 12 4zM4.3 11h3.8a18 18 0 0 0 0 2H4.3a8 8 0 0 1 0-2zm5 0h5.4a16 16 0 0 1 0 2H9.3a16 16 0 0 1 0-2zm6.6 0h3.8a8 8 0 0 1 0 2h-3.8a18 18 0 0 0 0-2zM9.2 15h5.6c-.5 3-1.8 5-2.8 5s-2.3-2-2.8-5z"/></svg>
      </li>
      <li class="address">
        <span>421, Address line goes here<br>45452, Country name</span>
        <svg viewBox="0 0 24 24" aria-hidden="true"><path d="M12 2a7 7 0 0 0-7 7c0 5 7 13 7 13s7-8 7-13a7 7 0 0 0-7-7zm0 9.5a2.5 2.5 0 1 1 0-5 2.5 2.5 0 0 1 0 5z"/></svg>
      </li>
    </ul>

    <div class="edge-band">
      <span class="edge-band__red"></span>
      <span class="edge-band__cyan"></span>
    </div>
  </section>

</body>
</html>
```